IT Services Company Needs Corporate PPT Template

This is urgent (need a fast turn around). We need a corporate PPT template deck (NOTE: Deck should be in 4:3 ratio) for our IT Services firm that is clean but slick and modern. We tend to lean more towards the flat design look. I'm attaching a zip file which includes our Corporate Branding Guide (which is in progress), color scheme, A PPT deck as inspiration (our logo is on the last slide), our font (LATO). Our newly launched website is located at: http://www.veranthix.com.

As an example of a deck we like see: http://slidemorrow.net/item/clean-multipurpose-business-presentation-template/5318206?WT.ac=category_thumb&WT.seg_1=category_thumb&WT.z_author=PixelHarbor
Although we don't want "this" deck - it gives an idea of style.

I'm also attaching a copy of our corporate deck as it is now to give you an idea of the type of content that would appear on various slides. We definitely want the following slides (at least) within the template:

Title Slide
Blank Slide
2 Column - with bullets
2 Column - no bullets
Single Column - no bullets
Single Column - with bullets
Various Charts and Tables (see example deck)
Meet the Team
Offering Slide
Customer Showcase
Timeline
Case Study
Contact US

Note: Being awarded this job will lead to a second job of creating our corporate deck.

Target Market(s)

CIO, CEO, Technology Officers, Sales People, Marketing, IT heads and staff, Customers, Prospective customers

Industry/Entity Type

Business

Requirements
Must have
• See description and attached files

```html
<!DOCTYPE html>
<html lang="en">
<head>
<meta charset="utf-8">
<title>Two Column Bullet Slide</title>
<link rel="stylesheet" href="https://fonts.googleapis.com/css2?family=Lato:wght@400;700;900&display=swap">
<style>
  :root {
    --header-teal: #0c5a7e;
    --header-teal-dark: #0a4d6c;
    --accent-cyan: #5bbad5;
    --bullet-navy: #173f6b;
    --text-body: #454545;
    --footer-grey: #e9e9ea;
    --footer-line: #d4d4d6;
    --brand-navy: #1b4683;
    --presenter-blue: #3a8fd4;
    --slide-white: #ffffff;
  }
  * { box-sizing: border-box; margin: 0; padding: 0; }
  html, body { width: 1200px; height: 900px; overflow: hidden; }
  body { font-family: "Lato", Arial, sans-serif; background: var(--slide-white); }

  .slide {
    position: relative;
    width: 1200px;
    height: 900px;
    overflow: hidden;
    background:
      radial-gradient(ellipse 520px 560px at 1060px 420px, rgba(225,228,234,0.55), rgba(255,255,255,0) 70%),
      var(--slide-white);
  }

  .slide-header {
    position: absolute; left: 0; top: 0;
    width: 1200px; height: 99px;
    background: linear-gradient(90deg, var(--header-teal-dark), var(--header-teal) 55%, #0e6288);
  }
  .project-title {
    position: absolute; left: 33px; top: 27px;
    font-size: 38px; font-weight: 700; color: #fff; line-height: 46px;
  }

  .section-title {
    position: absolute; left: 35px; top: 150px;
    font-size: 33px; font-weight: 700; color: var(--accent-cyan); line-height: 40px;
  }

  .bullet-column {
    position: absolute; top: 246px;
    list-style: none;
  }
  .bullet-column.left { left: 75px; }
  .bullet-column.right { left: 632px; }
  .bullet-item {
    display: flex; align-items: center;
    height: 33px; margin-bottom: 50.3px;
    font-size: 29px; color: var(--text-body);
  }
  .bullet-icon { width: 33px; height: 30px; margin-right: 25px; flex: none; }

  .slide-footer {
    position: absolute; left: 0; top: 816px;
    width: 1200px; height: 84px;
    background: linear-gradient(180deg, #f3f3f4, var(--footer-grey));
    border-top: 2px solid var(--footer-line);
    box-shadow: 0 -3px 6px rgba(0,0,0,0.06);
  }
  .brand-name {
    position: absolute; left: 24px; top: 21px;
    font-size: 38px; font-weight: 900; color: var(--brand-navy); line-height: 44px;
  }
  .presenter {
    position: absolute; right: 18px; top: 30px;
    display: flex; align-items: baseline; gap: 8px;
    color: var(--presenter-blue);
  }
  .presenter-label { font-size: 18px; }
  .presenter-name { font-size: 22px; font-weight: 700; }
</style>
</head>
<body>
<div class="slide">
  <header class="slide-header">
    <h1 class="project-title">Project Title here</h1>
  </header>

  <h2 class="section-title">2 Col slide title here</h2>

  <ul class="bullet-column left">
    <li class="bullet-item"><svg class="bullet-icon" viewBox="0 0 33 30"><rect width="33" height="30" fill="#173f6b"/><path d="M13 8l8 7-8 7" fill="none" stroke="#fff" stroke-width="4"/></svg>Bullet Slide Title Here</li>
    <li class="bullet-item"><svg class="bullet-icon" viewBox="0 0 33 30"><rect width="33" height="30" fill="#173f6b"/><path d="M13 8l8 7-8 7" fill="none" stroke="#fff" stroke-width="4"/></svg>Bullet Slide Title Here</li>
    <li class="bullet-item"><svg class="bullet-icon" viewBox="0 0 33 30"><rect width="33" height="30" fill="#173f6b"/><path d="M13 8l8 7-8 7" fill="none" stroke="#fff" stroke-width="4"/></svg>Bullet Slide Title Here</li>
    <li class="bullet-item"><svg class="bullet-icon" viewBox="0 0 33 30"><rect width="33" height="30" fill="#173f6b"/><path d="M13 8l8 7-8 7" fill="none" stroke="#fff" stroke-width="4"/></svg>Bullet Slide Title Here</li>
    <li class="bullet-item"><svg class="bullet-icon" viewBox="0 0 33 30"><rect width="33" height="30" fill="#173f6b"/><path d="M13 8l8 7-8 7" fill="none" stroke="#fff" stroke-width="4"/></svg>Bullet Slide Title Here</li>
    <li class="bullet-item"><svg class="bullet-icon" viewBox="0 0 33 30"><rect width="33" height="30" fill="#173f6b"/><path d="M13 8l8 7-8 7" fill="none" stroke="#fff" stroke-width="4"/></svg>Bullet Slide Title Here</li>
  </ul>

  <ul class="bullet-column right">
    <li class="bullet-item"><svg class="bullet-icon" viewBox="0 0 33 30"><rect width="33" height="30" fill="#173f6b"/><path d="M13 8l8 7-8 7" fill="none" stroke="#fff" stroke-width="4"/></svg>Bullet Slide Title Here</li>
    <li class="bullet-item"><svg class="bullet-icon" viewBox="0 0 33 30"><rect width="33" height="30" fill="#173f6b"/><path d="M13 8l8 7-8 7" fill="none" stroke="#fff" stroke-width="4"/></svg>Bullet Slide Title Here</li>
    <li class="bullet-item"><svg class="bullet-icon" viewBox="0 0 33 30"><rect width="33" height="30" fill="#173f6b"/><path d="M13 8l8 7-8 7" fill="none" stroke="#fff" stroke-width="4"/></svg>Bullet Slide Title Here</li>
    <li class="bullet-item"><svg class="bullet-icon" viewBox="0 0 33 30"><rect width="33" height="30" fill="#173f6b"/><path d="M13 8l8 7-8 7" fill="none" stroke="#fff" stroke-width="4"/></svg>Bullet Slide Title Here</li>
    <li class="bullet-item"><svg class="bullet-icon" viewBox="0 0 33 30"><rect width="33" height="30" fill="#173f6b"/><path d="M13 8l8 7-8 7" fill="none" stroke="#fff" stroke-width="4"/></svg>Bullet Slide Title Here</li>
    <li class="bullet-item"><svg class="bullet-icon" viewBox="0 0 33 30"><rect width="33" height="30" fill="#173f6b"/><path d="M13 8l8 7-8 7" fill="none" stroke="#fff" stroke-width="4"/></svg>Bullet Slide Title Here</li>
  </ul>

  <footer class="slide-footer">
    <div class="brand-name">Veranthix</div>
    <div class="presenter">
      <span class="presenter-label">Persentator Name&nbsp;&nbsp;:</span>
      <span class="presenter-name">Lena Torvalde</span>
    </div>
  </footer>
</div>
</body>
</html>
```